Retail Jewelry Business Card Design Project

We are in need of a new business card design for a retail jewelry store. This store is in the business of fine jewelry including but not specific to bridal jewelry, diamonds, designer jewelry and watches.

This store has been in business for 20 years but continues to strive for a modern professional appeal. The main colors use for this business are a royal blue, white and silver.

Target Market(s)

Target market is ages 18-50

Industry/Entity Type

Jewelry

Requirements
Must have
• Sales Person Name
Sales Person Email Address

Store Address
Store Phone
Website

Standard business card size. No odd shapes or sizes.
Nice to have
• Overall modern feel for card.

We have thought that a design with a nice feature of the logo on the back of the card would be nice but open to ideas.
Should not have
• No specific images of jewelry should be used.

```html
<!DOCTYPE html>
<html lang="en">
<head>
<meta charset="utf-8">
<title>Marlow Grant Fine Jewelry – Business Cards</title>
<link rel="stylesheet" href="https://fonts.googleapis.com/css2?family=Tinos:ital,wght@0,400;0,700;1,700&display=swap">
<style>
  :root {
    --royal-blue: #2e3192;
    --lavender: #8580c8;
    --card-white: #ffffff;
    --backdrop: #e6e7ec;
    --ink-grey: #555a66;
    --silver-edge: #c9cbd2;
  }
  * { margin: 0; padding: 0; box-sizing: border-box; }
  html, body { width: 1200px; height: 980px; overflow: hidden; }
  body {
    background: var(--backdrop);
    font-family: "Tinos", "Times New Roman", serif;
    position: relative;
  }
  .card {
    position: absolute;
    left: 250px;
    width: 700px;
    height: 400px;
    background: var(--card-white);
    border-radius: 34px;
    border: 1px solid var(--silver-edge);
    overflow: hidden;
  }
  .card--front { top: 60px; }
  .card--back  { top: 520px; }

  .wordmark {
    position: absolute;
    color: var(--royal-blue);
    font-weight: 700;
    text-align: center;
    line-height: 1;
  }
  .wordmark__name { font-size: 60px; display: block; letter-spacing: 1px; }
  .wordmark__trade { font-size: 30px; display: block; letter-spacing: 6px; margin-top: 12px; }
  .card--front .wordmark { left: 210px; top: 42px; width: 440px; }
  .card--back .wordmark { left: 0; top: 110px; width: 700px; }

  .wave { position: absolute; left: 0; top: 0; width: 700px; height: 400px; }

  .contact { position: absolute; left: 62px; top: 168px; color: #222; }
  .contact__person {
    color: var(--royal-blue);
    font-weight: 700;
    font-style: italic;
    font-size: 22px;
    margin-bottom: 10px;
  }
  .contact__line {
    display: flex;
    align-items: center;
    gap: 8px;
    font-size: 17px;
    line-height: 25px;
  }
  .contact__icon { width: 14px; height: 14px; flex: none; }
  .contact__line--web { padding-left: 22px; }

  .address {
    position: absolute;
    right: 44px;
    bottom: 26px;
    color: var(--card-white);
    font-size: 20px;
    line-height: 26px;
    text-align: right;
  }
  .site-url {
    position: absolute;
    left: 0;
    top: 248px;
    width: 700px;
    text-align: center;
    color: var(--ink-grey);
    font-size: 18px;
    letter-spacing: 5px;
  }
</style>
</head>
<body>

  <section class="card card--front" aria-label="Business card front">
    <svg class="wave" viewBox="0 0 700 400" aria-hidden="true">
      <path d="M0,212 C55,352 235,382 445,322 C565,292 650,300 700,326 L700,400 L0,400 Z" fill="var(--lavender)"/>
      <path d="M0,236 C58,372 238,402 448,344 C568,312 652,320 700,348 L700,400 L0,400 Z" fill="var(--royal-blue)"/>
    </svg>

    <div class="wordmark">
      <span class="wordmark__name">Marlow Grant</span>
      <span class="wordmark__trade">FINE JEWELRY</span>
    </div>

    <div class="contact">
      <p class="contact__person">Marlow Grant Ellison</p>
      <p class="contact__line">
        <svg class="contact__icon" viewBox="0 0 14 14" aria-hidden="true">
          <circle cx="7" cy="7" r="7" fill="var(--royal-blue)"/>
          <path d="M4.5,3.5 L6,3.5 L6.6,5.4 L5.7,6.1 C6.2,7.1 6.9,7.8 7.9,8.3 L8.6,7.4 L10.5,8 L10.5,9.5 C7,9.8 4.2,7 4.5,3.5 Z" fill="#fff"/>
        </svg>
        555-014-2860
      </p>
      <p class="contact__line">
        <svg class="contact__icon" viewBox="0 0 14 14" aria-hidden="true">
          <circle cx="7" cy="7" r="7" fill="var(--royal-blue)"/>
          <rect x="3.5" y="4.5" width="7" height="5" fill="#fff"/>
          <path d="M3.5,4.5 L7,7.3 L10.5,4.5" fill="none" stroke="var(--royal-blue)" stroke-width="0.9"/>
        </svg>
        marlow@marlowgrantjewelry.com
      </p>
      <p class="contact__line">
        <svg class="contact__icon" viewBox="0 0 14 14" aria-hidden="true">
          <circle cx="7" cy="7" r="7" fill="var(--royal-blue)"/>
          <circle cx="7" cy="7" r="4" fill="none" stroke="#fff" stroke-width="0.9"/>
          <ellipse cx="7" cy="7" rx="1.8" ry="4" fill="none" stroke="#fff" stroke-width="0.9"/>
          <line x1="3" y1="7" x2="11" y2="7" stroke="#fff" stroke-width="0.9"/>
        </svg>
        www.marlowgrantjewelry.com
      </p>
    </div>

    <address class="address" style="font-style: normal;">
      2280 Linden Avenue<br>
      Harbor Point, FL 32990
    </address>
  </section>

  <section class="card card--back" aria-label="Business card back">
    <div class="wordmark">
      <span class="wordmark__name">Marlow Grant</span>
      <span class="wordmark__trade">FINE JEWELRY</span>
    </div>
    <p class="site-url">www.marlowgrantjewelry.com</p>
  </section>

</body>
</html>
```